Homepage mockup for RoutineVerdict.com

I would like a homepage mockup of routineverdict.com.

Basically what the site does, is it allows a person to upload a video of a gymnastics routine and our certified judges will judge the routine providing a score, as well as provide a critique and feedback as to why they gave you that score. Many times people don't know why they got the score they did at a gymnastics competition, so this site aims to provide reasoning behind it.

I have started to design the homepage myself (see attached), and like it, but I'd like a professional to finish the layout, or even come up with something really wow and original. I like clean, typically simple design.

THIS IS AN OLD VERSION OF THE SITE (http://esite.kelpradia.com/) This should only be used so you can get an idea of what the site is about. I DO NOT want the new site to look like this, but the basic concept and content remains the same.

DESIGNER FILES CAN BE DOWNLOADED HERE (http://kelpradia.com/files.aspx)

Target Market(s)

Gymnastic type people, parents of gymnasts, coaches, etc.

Industry/Entity Type

It Professional

Requirements
Must have
• -Routine verdict logo (provided)
-Not required, but I have attached the main photo I used in my mockup (AI File)
*A step by step graphic(s) depicting the process for a user. A How it works sort of explanation. Should be eye catching, not just text.

-Step 1: Videotape your gymnastic routine.
-Step 2: Create an account and share us your video.
-Step 3: Our certified judges will score and critique your routine, fully explaining the reasons behind their score.

```html
<!DOCTYPE html>
<html lang="en">
<head>
<meta charset="utf-8">
<title>RoutineVerdict.com</title>
<link href="https://fonts.googleapis.com/css2?family=Ubuntu:wght@400;500;700&family=Ubuntu+Condensed&family=Play:wght@400;700&display=swap" rel="stylesheet">
<style>
:root{
  --page:#f0f0f0;
  --white:#ffffff;
  --blue:#1f66d6;
  --blue-dark:#1350b3;
  --blue-card:#185fa8;
  --red:#d8121c;
  --red-dark:#a80a12;
  --ink:#222222;
  --grey-card:#e9e9e9;
  --grey-line:#cfcfcf;
  --bar:#4a4a4a;
  --black:#050505;
}
*{margin:0;padding:0;box-sizing:border-box}
html,body{width:1200px;height:964px;overflow:hidden}
body{background:var(--page);font-family:'Ubuntu',sans-serif;color:var(--ink);position:relative}
.header{position:absolute;left:0;top:0;width:1200px;height:160px;background:var(--white)}
.brand{position:absolute;left:135px;top:30px;display:flex;align-items:center;gap:10px}
.brand-dot{width:30px;height:30px;border-radius:50%;background:var(--blue)}
.brand-name{font-family:'Ubuntu',sans-serif;font-weight:700;font-size:30px;color:var(--blue-dark);line-height:1}
.login-bar{position:absolute;left:570px;top:0;width:520px;height:42px;background:var(--bar);border-radius:0 0 10px 10px;clip-path:polygon(0 0,100% 0,100% 100%,50px 100%);display:flex;align-items:center;padding-left:45px;gap:6px;font-size:12px;color:#fff}
.login-bar input{width:155px;height:30px;border:0;border-radius:4px;font:10px 'Ubuntu',sans-serif;padding-left:9px;color:#222;margin-right:4px}
.login-bar .login-btn{font-size:14px;margin-left:4px;color:#eee}
.nav{position:absolute;left:112px;top:101px;width:982px;height:45px;background:linear-gradient(#2b77e6,var(--blue-dark));border-radius:3px 3px 0 0}
.nav-home{position:absolute;left:31px;top:8px;width:34px;height:37px;background:#3d84e6;display:flex;align-items:center;justify-content:center}
.nav-links{position:absolute;left:87px;top:0;display:flex;height:45px}
.nav-links a{font-family:'Ubuntu Condensed',sans-serif;font-size:17px;color:#fff;text-decoration:none;line-height:50px;padding:0 20px;border-left:1px solid rgba(255,255,255,.15)}
.search{position:absolute;left:776px;top:9px;display:flex}
.search input{width:151px;height:26px;border:0;font:12px 'Ubuntu',sans-serif;padding-left:8px;color:#222}
.search button{width:32px;height:26px;border:0;background:var(--red);display:flex;align-items:center;justify-content:center}
.main{position:absolute;left:112px;top:160px;width:980px;height:745px;background:var(--white)}
.hero{position:absolute;left:18px;top:1px;width:942px;height:395px;background:linear-gradient(115deg,#1a5fd0,#2e7ae8 60%,#1b5ccc)}
.video{position:absolute;left:14px;top:17px;width:576px;height:362px;background:#000;border-radius:4px;overflow:hidden}
.video-still{position:absolute;inset:0;background:radial-gradient(ellipse at 45% 50%,#4a3050,#1a1030 55%,#07061a)}
.play-big{position:absolute;left:241px;top:102px;width:108px;height:107px;border-radius:10px;background:linear-gradient(#e0242c,var(--red-dark))}
.controls{position:absolute;left:46px;top:297px;width:487px;height:55px;border-radius:6px;background:linear-gradient(#3a3a3a,#1c1c1c)}
.ctrl-play{position:absolute;left:30px;top:11px;width:33px;height:33px;border-radius:4px;background:var(--red)}
.track{position:absolute;left:78px;top:24px;width:288px;height:9px;border-radius:5px;background:#ddd}
.track-fill{position:absolute;left:0;top:0;width:96px;height:9px;border-radius:5px;background:#888}
.track-knob{position:absolute;left:48px;top:-5px;width:7px;height:19px;background:var(--red)}
.vol{position:absolute;left:378px;top:12px;display:flex;align-items:flex-end;gap:3px;height:22px}
.vol span{width:7px;background:var(--red)}
.steps{position:absolute;left:612px;top:67px}
.step{position:relative;width:316px;height:72px;margin-bottom:16px}
.step-icon{position:absolute;left:0;top:0;width:72px;height:72px;border-radius:50%;background:radial-gradient(circle at 40% 35%,#7fb3e8,#1d4f99);border:3px solid #e8eef6}
.step-label{position:absolute;left:78px;top:13px;width:235px;height:58px;border-radius:0 14px 14px 26px;background:linear-gradient(#ea2229,#c40d15);color:#fff;font-family:'Play',sans-serif;font-size:20px;line-height:58px;padding-left:20px}
.card{position:absolute;top:413px;width:300px;height:125px;border-radius:4px;padding:10px 9px}
.card h3{font-family:'Play',sans-serif;font-weight:400;font-size:18px;line-height:19px}
.card p{font-size:11px;line-height:14px;margin-top:8px;width:160px}
.card-icon{position:absolute;right:30px;top:30px;width:60px;height:64px;border-radius:8px}
.card-upload{left:23px;background:var(--blue-card);border:1px solid #0f4c8c;color:#fff}
.card-judge{left:335px;background:var(--grey-card);border:1px solid #d4d4d4}
.card-why{left:650px;background:var(--grey-card);border:1px solid #d4d4d4}
.divider{position:absolute;left:25px;top:558px;width:938px;height:2px;background:#ddd}
.intro h2{position:absolute;left:25px;top:566px;font-family:'Play',sans-serif;font-weight:400;font-size:24px;color:#c0141b}
.intro p{position:absolute;left:27px;width:925px;font-size:11.4px;font-weight:500;line-height:14.5px;color:#222}
.footer{position:absolute;left:112px;top:905px;width:980px;height:59px;background:var(--black);color:#fff}
.footer-links{position:absolute;left:27px;top:11px;font-size:12px}
.footer-links a{color:#fff;text-decoration:none}
.footer-links .sep{margin:0 13px}
.copyright{position:absolute;left:27px;top:36px;font-size:9.5px}
.follow{position:absolute;left:838px;top:10px;font-size:12px;font-weight:700}
.social{position:absolute;left:838px;top:29px;display:flex;gap:5px}
.social span{width:22px;height:22px;border-radius:3px}
</style>
</head>
<body>
<header class="header">
  <div class="brand"><span class="brand-dot"></span><span class="brand-name">Routine Verdict</span></div>
  <form class="login-bar">
    <label>Email:</label><input type="text" placeholder="Enter your Email">
    <label>Password:</label><input type="password" placeholder="Enter your Password">
    <span class="login-btn">Login</span>
  </form>
  <nav class="nav">
    <div class="nav-home"><svg width="16" height="15" viewBox="0 0 16 15"><path d="M8 0 0 7h2v8h4v-5h4v5h4V7h2z" fill="#fff"/></svg></div>
    <div class="nav-links"><a>How it work</a><a>FAQ</a><a>Sample Critique</a><a>Member Area</a><a>About</a></div>
    <div class="search"><input type="text" placeholder="Search ..."><button type="button"><svg width="14" height="14" viewBox="0 0 14 14"><circle cx="5" cy="5" r="3.5" fill="none" stroke="#fff" stroke-width="2"/><path d="M8 8l5 5" stroke="#fff" stroke-width="2.5"/></svg></button></div>
  </nav>
</header>

<main class="main">
  <section class="hero">
    <div class="video">
      <div class="video-still" role="img" aria-label="Gymnast performing a split leap in a dark arena"></div>
      <div class="play-big"><svg width="108" height="107" viewBox="0 0 108 107"><path d="M26 30 88 54 26 78 40 54z" fill="#e8e8e8"/></svg></div>
      <div class="controls">
        <div class="ctrl-play"><svg width="33" height="33" viewBox="0 0 33 33"><path d="M8 9l18 7.5L8 24l4-7.5z" fill="#fff"/></svg></div>
        <div class="track"><div class="track-fill"></div><div class="track-knob"></div></div>
        <div class="vol"><span style="height:7px"></span><span style="height:11px"></span><span style="height:16px"></span><span style="height:21px;background:#777"></span></div>
        <svg style="position:absolute;left:434px;top:16px" width="18" height="18" viewBox="0 0 18 18"><path d="M1 1h5M1 1v5M17 1h-5M17 1v5M1 17h5M1 17v-5M17 17h-5M17 17v-5M1 1l5 5M17 1l-5 5M1 17l5-5M17 17l-5-5" stroke="#ddd" stroke-width="1.6" fill="none"/></svg>
      </div>
    </div>
    <div class="steps">
      <div class="step"><div class="step-label">Record Your Routine</div><div class="step-icon" role="img" aria-label="Microphone icon"></div></div>
      <div class="step"><div class="step-label">Sign Up &amp; Upload</div><div class="step-icon" role="img" aria-label="Upload icon"></div></div>
      <div class="step"><div class="step-label">Get The “Why“</div><div class="step-icon" role="img" aria-label="Question mark icon"></div></div>
    </div>
  </section>

  <article class="card card-upload">
    <h3>Upload Your Video</h3>
    <p>Lorem ipsum dolar sit amet dolor infi nums te ardorLorem ipsum dolar sit amet dolor infi nums te ardorLorem ipsum dolar sit</p>
    <div class="card-icon" role="img" aria-label="Folder with upload arrow" style="background:linear-gradient(#6fc24a,#5b8fd0)"></div>
  </article>
  <article class="card card-judge">
    <h3>We’ll judge Your Routine</h3>
    <p>Lorem ipsum dolar sit amet dolor infi nums te ardorLorem ipsum dolar sit amet dolor infi nums te ardorLorem ipsum dolar sit</p>
    <div class="card-icon" role="img" aria-label="Two judges" style="background:linear-gradient(#f0b060,#6aa8e0)"></div>
  </article>
  <article class="card card-why">
    <h3>Get the “why” &amp; much much More</h3>
    <p style="margin-top:2px">Lorem ipsum dolar sit amet dolor infi nums te ardorLorem ipsum dolar sit amet dolor infi nums te ardor</p>
    <div class="card-icon" role="img" aria-label="Notebook with notes" style="background:linear-gradient(#b08040,#e8d890)"></div>
  </article>

  <div class="divider"></div>
  <section class="intro">
    <h2>Being Judged has hever been easier</h2>
    <p style="top:606px">Lorem Ipsum is simply dummy text of the printing and typesetting industry.Lorem Ipsum is simply dummy text.Lorem Ipsum is simply dummy text of the printing and typesetting industry.Lorem Ipsum is simply dummy text.Lorem Ipsum is simply dummy text of the printing and typesetting industry.Lorem Ipsum is simply dummy text.Lorem Ipsum is simply dummy text of the printing and typesetting industry.Lorem Ipsum is simply dummy text.Lorem Ipsum is simply dummy text of the printing and typesetting industry.Lorem Ipsum is simply dummy text.Lorem Ipsum is simply dummy text of the printing and typesetting industry.Lorem Ipsum is simply dummy text.Lorem Ipsum is simply dummy text of the printing and typesetting industry.Lorem Ipsum is simply dummy text.</p>
    <p style="top:693px">Lorem Ipsum is simply dummy text of the printing and typesetting industry.Lorem Ipsum is simply dummy text.Lorem Ipsum is simply dummy text of the printing and typesetting industry.Lorem Ipsum is simply dummy text.</p>
  </section>
</main>

<footer class="footer">
  <div class="footer-links"><a>Home</a><span class="sep">|</span><a>How it Work</a><span class="sep">|</span><a>FAQ</a><span class="sep">|</span><a>Sample ciritique</a><span class="sep">|</span><a>Member Area</a><span class="sep">|</span><a>About</a></div>
  <div class="copyright">Copyright © 2012 RoutineVerdict.com.All Right Reserved.</div>
  <div class="follow">Follow Us:</div>
  <div class="social"><span style="background:#3b5a9a"></span><span style="background:#3aa6dc"></span><span style="background:#1b7ab8"></span><span style="background:#e8822a"></span></div>
</footer>
</body>
</html>
```